Business Card Design

Need a new business card to represent our legal vertical focus. attached is an example of our old business card and newest logo. we would like the card to also identify "Legal Tech" as a tag line of business.

Our new address is
4817 Marlowe Hatchfield Rd.
Suite 518
Cincinnati, OH 45917

we no longer have a fax number.

Target Market(s)

Tech Consulting for Law Firms

Industry/Entity Type

Legal

Contact Information for Business Card

should use logo and colors. we are a b2b company

Font styles to use
Other font styles liked:
• tahoma

Requirements
Must have
• all print should be in lower case just as shown in photos. tag line should not
Should not have
• pinstripes or drop shadows

```html
<!DOCTYPE html>
<html lang="en">
<head>
<meta charset="utf-8">
<title>BraidLink Legal Tech – Business Card</title>
<link href="https://fonts.googleapis.com/css2?family=PT+Sans:wght@400;700&display=swap" rel="stylesheet">
<style>
  :root {
    --backdrop: #3b3431;
    --card: #1b1b1c;
    --card-back: #161617;
    --brand-blue: #2f4195;
    --brand-orange: #ef5a26;
    --tag-grey: #6f6f72;
    --mark-grey: #77767a;
    --text-light: #f2f2f2;
    --rule: #3c3c3f;
  }
  * { margin: 0; padding: 0; box-sizing: border-box; }
  html, body { width: 1200px; height: 844px; overflow: hidden; }
  body {
    background: var(--backdrop);
    font-family: "PT Sans", Tahoma, sans-serif;
    position: relative;
  }
  .card {
    position: absolute;
    top: 272px;
    width: 520px;
    height: 300px;
    border-radius: 3px;
  }
  .card--front { left: 60px; background: var(--card); }
  .card--back { left: 620px; background: var(--card-back); }

  .brand { position: absolute; display: flex; align-items: center; gap: 10px; }
  .brand__square { width: 26px; height: 26px; background: var(--brand-orange); }
  .brand__name { font-weight: 700; font-size: 56px; line-height: 1; letter-spacing: -1px; color: var(--brand-blue); }
  .brand__tagline { position: absolute; font-size: 22px; color: var(--tag-grey); }

  .card--front .brand { left: 150px; top: 52px; }
  .card--front .brand__tagline { right: 42px; top: 116px; }

  .person { position: absolute; left: 40px; top: 182px; }
  .person__name { font-size: 25px; font-weight: 700; color: var(--brand-orange); line-height: 1; }
  .person__role { font-size: 17px; color: var(--brand-blue); margin-top: 3px; margin-left: 44px; }
  .person__address { font-size: 17px; color: var(--text-light); line-height: 1.2; margin-top: 10px; }

  .divider { position: absolute; left: 290px; top: 168px; width: 1px; height: 100px; background: var(--rule); }

  .contacts { position: absolute; left: 306px; top: 168px; list-style: none; }
  .contacts li { display: flex; align-items: center; gap: 12px; font-size: 16px; color: var(--text-light); height: 24px; }
  .contacts .icon { width: 16px; height: 16px; background: var(--brand-blue); display: flex; align-items: center; justify-content: center; }

  .card--back .brand { left: 150px; top: 110px; }
  .card--back .brand__name { color: var(--mark-grey); }
  .card--back .brand__square { background: var(--mark-grey); }
  .card--back .brand__tagline { right: 80px; top: 174px; color: #555558; }
</style>
</head>
<body>
  <section class="card card--front">
    <div class="brand">
      <span class="brand__square"></span>
      <span class="brand__name">BraidLink</span>
    </div>
    <span class="brand__tagline">Legal Tech</span>

    <div class="person">
      <p class="person__name">daniel reyes</p>
      <p class="person__role">managing director</p>
      <p class="person__address">12345, address agoes here<br>country name, 123456</p>
    </div>

    <div class="divider"></div>

    <ul class="contacts">
      <li><span class="icon"><svg width="10" height="10" viewBox="0 0 10 10"><path d="M1 3c0-1 1-2 2-2l1 2-1 1c1 1 2 2 3 3l1-1 2 1c0 1-1 2-2 2C4 9 1 6 1 3z" fill="#fff"/></svg></span>(044)-456-7890</li>
      <li><span class="icon"><svg width="10" height="10" viewBox="0 0 10 10"><rect x="3" y="1" width="4" height="8" rx="1" fill="#fff"/></svg></span>123-456-7890</li>
      <li><span class="icon"><svg width="10" height="10" viewBox="0 0 10 10"><rect x="1" y="2" width="8" height="6" fill="#fff"/><path d="M1 2l4 3 4-3" stroke="#2f4195" fill="none"/></svg></span>info@youremail.com</li>
      <li><span class="icon"><svg width="10" height="10" viewBox="0 0 10 10"><path d="M3 7l4-4M2 6l-1 1 2 2 1-1M8 4l1-1-2-2-1 1" stroke="#fff" fill="none"/></svg></span>www.website.com</li>
    </ul>
  </section>

  <section class="card card--back">
    <div class="brand">
      <span class="brand__square"></span>
      <span class="brand__name">BraidLink</span>
    </div>
    <span class="brand__tagline">Legal Tech</span>
  </section>
</body>
</html>
```